Aquatic View

We need a web design for a new window cleaning company name Tidewell Glass Care. We are located in Grand Cayman, Cayman Islands. We are a small company, a team of husband and wife. Our services include residencial interior and exterior window cleaning and commercial. Extra services such as ceiling fans cleaning, mirrors, high dusting. Home cleaning services. Power washing. Explaining the service. We want a modern, beachy style with aquatic colors. We want to use our domain name "tidewellglasscare.ky". We want to portray a clean, modern and professional design.

Target Market(s)

Big Home owners

Industry/Entity Type

Cleaning Service

Contact Information for Business Card

Company Name: Tidewell Glass Care
Name: Desmond Farrowby owner/manager
Phone: 345-9170452
Email: desmond@tidewellglasscare.ky
Website: tidewellglasscare.ky
Address: P.O.Box 2486 GT, George Town, Grand Cayman KY1-1203 Cayman Islands

Number of Pages Required

2 page

Font styles to use
Sans Serif

Colors
0592cd
0455a3
33a6d7
85cae6
cadf82
abd036
fbf289

Requirements
Nice to have
• Pictures of an ocean view and palm trees from clear windows.
• https://quorvantel.com/bidlinker/
• Use the above for "free estimate".

```html
<!DOCTYPE html>
<html lang="en">
<head>
<meta charset="utf-8">
<title>Tidewell Glass Care</title>
<link href="https://fonts.googleapis.com/css2?family=Lato:ital,wght@0,400;0,700;0,900;1,400&display=swap" rel="stylesheet">
<style>
:root{
  --topbar:#333333;
  --ink:#333333;
  --body:#666666;
  --red:#b8000e;
  --blue:#0592cd;
  --blue-deep:#0455a3;
  --line:#d9d9d9;
  --footer:#2d2d2d;
}
*{margin:0;padding:0;box-sizing:border-box}
html,body{width:1200px;height:1001px;overflow:hidden}
body{position:relative;font-family:'Lato',sans-serif;background:#fff;color:var(--body)}
.abs{position:absolute}
.topbar{left:0;top:0;width:1200px;height:36px;background:var(--topbar)}
.topbar .phone{right:116px;top:4px;display:flex;align-items:center;gap:6px;color:#fff;font-weight:700;font-size:19px}
.header{left:0;top:36px;width:1200px;height:67px;background:#fff}
.brand{left:124px;top:9px;width:140px;height:80px;background:#fff;border-radius:70px 70px 0 0;display:flex;flex-direction:column;align-items:center;justify-content:flex-end;padding-bottom:8px}
.brand-mark{width:36px;height:36px;border-radius:50%;background:var(--blue);margin-bottom:6px}
.brand-name{font-weight:900;font-size:14px;color:var(--ink);white-space:nowrap}
.nav{left:728px;top:62px;display:flex;align-items:center;font-size:13px;font-weight:700;color:var(--ink)}
.nav a{color:inherit;text-decoration:none;padding:0 13px;height:22px;line-height:20px;border-left:1px solid #ccc}
.nav a:first-child{border:1px solid var(--blue);color:var(--blue);margin-right:0}
.nav a:nth-child(2){border-left:none}
.nav a:last-child{padding-left:20px}
.hero{left:0;top:103px;width:1200px;height:441px;background:linear-gradient(90deg,#c6c4dc 0%,#d6cbd6 35%,#8f7f8a 55%,#3d3438 68%,#65728a 100%)}
.hero-title{left:118px;top:252px;font-size:25px;font-weight:900;line-height:36px;color:var(--ink);letter-spacing:.3px}
.arrow{width:40px;height:40px;border-radius:50%;background:#e6e6e6;border:3px solid #cfcfcf;display:flex;align-items:center;justify-content:center}
.backdrop{left:0;top:544px;width:1200px;height:230px;background:linear-gradient(#e0e0e0,#fff)}
.panel{left:99px;top:506px;width:1002px;height:349px;background:#fff;box-shadow:0 0 12px rgba(0,0,0,.12)}
.col-head{font-size:17px;font-weight:900;letter-spacing:.3px;padding-bottom:8px;border-bottom:1px solid var(--line);position:relative}
.col-head::after{content:"";position:absolute;left:0;bottom:-2px;width:86px;height:3px;background:var(--blue-deep)}
.col-head .r{color:var(--red)}.col-head .b{color:var(--blue)}
.divider{width:1px;background:#eee;top:543px;height:262px}
.photo{left:116px;top:578px;width:265px;height:121px;border:1px solid #bbb;background:linear-gradient(110deg,#9cc0dc,#eaeef2 55%,#c9b69a)}
p{font-size:13px;line-height:19.5px}
.btn{background:linear-gradient(#1a6fc2,#0455a3);color:#fff;font-weight:700;font-size:13.5px;display:flex;align-items:center;justify-content:center}
.svc-title{display:flex;align-items:center;gap:7px;color:var(--blue);font-weight:700;font-size:15px;margin:2px 0 0 -2px}
.field{border:1px solid #ccc;font-size:12px;color:#555;padding:6px 6px}
.footer{left:0;top:855px;width:1200px;height:107px;background:var(--footer);color:#fff}
.flinks{left:117px;top:20px;font-size:13px;font-weight:700;display:flex;gap:14px}
.finfo{font-size:13px;display:flex;align-items:center;gap:7px}
.sub{left:842px;top:19px;width:242px;height:30px;background:#fff;display:flex}
.sub span{flex:1;font-size:11px;font-style:italic;color:#888;padding:8px 0 0 28px}
.sub b{width:84px;background:var(--blue-deep);font-size:13px;display:flex;align-items:center;justify-content:center}
.social{width:24px;height:24px;border:1.5px solid #fff;border-radius:50%}
.copy{left:0;top:962px;width:1200px;height:39px;background:linear-gradient(#0a86cc,#0455a3);color:#fff;font-size:13px;display:flex;align-items:center;justify-content:center}
</style>
</head>
<body>
<div class="abs topbar">
  <div class="abs phone">
    <svg width="27" height="27" viewBox="0 0 27 27"><circle cx="13.5" cy="13.5" r="12" fill="none" stroke="#fff" stroke-width="1.5"/><path d="M9 8c1-1 2-1 2.5 0l1 2c.3.6 0 1-.5 1.4-.5.4-.3 1 .3 1.8.7.9 1.4 1.5 2 1.7.5.2 1-.1 1.3-.6.4-.5 1-.6 1.5-.2l1.8 1.2c.7.5.6 1.3-.2 2-1.5 1.3-4 .8-6.5-1.7S8 9.4 9 8z" fill="#fff"/></svg>
    012-555-0148
  </div>
</div>
<div class="abs header"></div>
<div class="abs brand"><div class="brand-mark"></div><div class="brand-name">Tidewell Glass Care</div></div>
<nav class="abs nav"><a>HOME</a><a>ABOUT US</a><a>SERIVCES</a><a>CONTACT US</a></nav>

<div class="abs hero" role="img" aria-label="Window cleaners on ropes silhouetted against a glass tower at dusk"></div>
<div class="abs hero-title">WE ARE<br>RESIDENTIAL,COMMERCIAL<br>CLEANING SERVICE FIRM</div>
<div class="abs arrow" style="left:31px;top:297px"><svg width="12" height="14"><path d="M9 1 3 7l6 6" fill="none" stroke="#555" stroke-width="2.5"/></svg></div>
<div class="abs arrow" style="left:1128px;top:297px;background:#d0d0d0;border-color:#bbb"><svg width="12" height="14"><path d="M3 1l6 6-6 6" fill="none" stroke="#555" stroke-width="2.5"/></svg></div>

<div class="abs backdrop"></div>
<div class="abs panel"></div>

<div class="abs" style="left:116px;top:531px;width:273px"><div class="col-head"><span class="r">ABOUT</span> <span class="b">TIDEWELL GLASS CARE</span></div></div>
<div class="abs photo" role="img" aria-label="Worker in a blue cap squeegeeing a large window"></div>
<p class="abs" style="left:117px;top:707px;width:265px">Lorem ipsum dolor sit amet, consectetuer adip iscing elit, sed diam nonummy nibh euismod magna aliquam erat volutpat.</p>
<div class="abs btn" style="left:116px;top:774px;width:94px;height:31px">READ MORE</div>
<div class="abs divider" style="left:407px"></div>

<div class="abs" style="left:433px;top:532px;width:334px"><div class="col-head"><span class="r">OUR</span> <span class="b">SERVICES</span></div></div>
<div class="abs" style="left:435px;top:574px;width:330px">
  <p>Lorem ipsum dolor sit amet, consectetuer adip iscing elit sed diam nonummy nibh euismod magna.</p>
  <div class="svc-title" style="margin-top:5px"><svg width="20" height="18"><path d="M10 1 1 9h3v8h5v-5h2v5h5V9h3z" fill="#666"/></svg>Residential</div>
  <p>Lorem ipsum dolor sit amet, consectetuer adip iscing elit sed diam nonummy nibh euismod magna.</p>
  <div class="svc-title" style="margin-top:5px"><svg width="20" height="18"><path d="M2 17V7h5V2h6v7h5v8z" fill="#666"/><path d="M9 4h2M9 7h2M9 10h2M4 10h2M15 12h2" stroke="#fff"/></svg>Commercial</div>
  <p>Lorem ipsum dolor sit amet, consectetuer adip iscing elit sed diam nonummy nibh euismod magna.</p>
  <div class="svc-title" style="margin-top:9px"><svg width="20" height="18"><circle cx="7" cy="7" r="5" fill="none" stroke="#666" stroke-width="3"/><circle cx="15" cy="13" r="3" fill="none" stroke="#666" stroke-width="2.5"/></svg>Extra Services</div>
  <p>Lorem ipsum dolor sit amet, consectetuer adip iscing elit sed diam nonummy nibh euismod magna.</p>
</div>
<div class="abs divider" style="left:792px"></div>

<div class="abs" style="left:817px;top:532px;width:265px"><div class="col-head"><span class="r">QUICK</span> <span class="b">INQUIRY</span></div></div>
<svg class="abs" style="left:1058px;top:539px" width="24" height="10"><path d="M5 1 1 5l4 4M19 1l4 4-4 4" fill="none" stroke="#333" stroke-width="1.2"/></svg>
<div class="abs field" style="left:817px;top:580px;width:265px;height:30px">Email</div>
<div class="abs field" style="left:817px;top:617px;width:265px;height:30px">Phone</div>
<div class="abs field" style="left:817px;top:655px;width:265px;height:30px">Email</div>
<div class="abs field" style="left:817px;top:693px;width:265px;height:72px">Message</div>
<div class="abs btn" style="left:817px;top:774px;width:90px;height:31px">SUBMIT</div>

<footer class="abs footer">
  <div class="abs flinks"><span>Home</span><span>I</span><span>About Us</span><span>I</span><span>Serivces</span><span>&nbsp;I</span><span>Contact Us</span></div>
  <div class="abs finfo" style="left:117px;top:48px"><svg width="12" height="15"><path d="M6 14C2 9 1 7 1 5a5 5 0 0 1 10 0c0 2-1 4-5 9z" fill="#aaa"/><circle cx="6" cy="5" r="1.8" fill="#2d2d2d"/></svg>Lorem ipsum dolor sit amet consectetuer adimpisciged</div>
  <div class="abs finfo" style="left:115px;top:72px"><svg width="17" height="17"><circle cx="8.5" cy="8.5" r="7.5" fill="none" stroke="#aaa"/><path d="M6 5c.6-.6 1.2-.6 1.5 0l.6 1.2c.2.4 0 .6-.3.9-.3.3 0 .8.6 1.4s1.1.8 1.4.5c.3-.3.6-.4 1-.2l1.1.8c.4.3.4.8-.1 1.2-1 .8-2.5.5-4-1S5.4 5.6 6 5z" fill="#aaa"/></svg>123-555-0192 <svg width="12" height="9" style="margin-left:6px"><rect x=".5" y=".5" width="11" height="8" fill="#aaa"/><path d="M.5.5 6 5l5.5-4.5" fill="none" stroke="#2d2d2d"/></svg>info@harbourlinesupply.com</div>
  <div class="abs sub"><span>your e-mail address</span><b>SUBSCRIBE</b></div>
  <div class="abs social" style="left:968px;top:67px"></div>
  <div class="abs social" style="left:1000px;top:67px"></div>
  <div class="abs social" style="left:1030px;top:67px"></div>
  <div class="abs social" style="left:1059px;top:67px"></div>
</footer>
<div class="abs copy">Copyright © 2015&nbsp; Tidewell Glass Care. All Right Reserved</div>
</body>
</html>
```